Tech business card design

We need an amazing business card design for our new business 'Pexla' a marketing tech startup based in Sydney, Australia. We provide an online marketplace for businesses to search and buy advertising media, connect with service providers and learn more about marketing. We wish to communicate 'cool tech', reliability and professionalism and design based around our logo.

Target Market(s)

Business Owners

Contact Information for Business Card

Name
Position
Email Address
Website
Phone Number

Font styles to use
Other font styles liked:
• Avenir & Avenir Next

Colors

Designer to choose colors to be used in the design.

```html
<!DOCTYPE html>
<html lang="en">
<head>
<meta charset="utf-8">
<title>Pexla Business Card</title>
<link rel="stylesheet" href="https://fonts.googleapis.com/css2?family=Nunito+Sans:wght@400;700;900&display=swap">
<style>
  :root {
    --backdrop: #1d1e20;
    --paper: #ffffff;
    --navy: #14153f;
    --slate: #6d6e72;
    --ink: #1a1a1a;
    --on-dark: #ffffff;
  }
  * { margin: 0; padding: 0; box-sizing: border-box; }
  html, body {
    width: 1200px; height: 803px; overflow: hidden;
    background: var(--backdrop);
    font-family: "Nunito Sans", Arial, sans-serif;
  }
  .stage {
    position: relative; width: 1200px; height: 803px;
    display: flex; align-items: center; justify-content: center; gap: 50px;
  }
  .card {
    position: relative; width: 540px; height: 309px; overflow: hidden;
    box-shadow: 0 14px 30px rgba(0,0,0,.55);
  }
  .card--front { background: var(--paper); }
  .card--back {
    background: var(--slate);
    display: flex; align-items: center; justify-content: center;
  }

  .brand-name {
    font-weight: 900; color: var(--navy); letter-spacing: -1px; line-height: 1;
  }
  .card--front .brand-name {
    position: absolute; left: 30px; top: 28px; font-size: 78px;
  }
  .card--back .brand-name { font-size: 110px; }

  .contact-band {
    position: absolute; left: 292px; top: 108px; width: 248px; height: 84px;
    background: var(--navy);
  }
  .icon-strip {
    position: absolute; left: 264px; top: 108px; width: 28px; height: 84px;
    background: var(--slate);
  }
  .icon-list, .contact-list {
    position: absolute; top: 116px; list-style: none;
  }
  .icon-list { left: 264px; width: 28px; }
  .contact-list { left: 302px; }
  .icon-list li {
    height: 22px; display: flex; align-items: center; justify-content: center;
  }
  .icon-list svg { width: 13px; height: 13px; }
  .contact-list li {
    height: 22px; line-height: 22px;
    color: var(--on-dark); font-size: 13px; white-space: nowrap;
  }

  .name-band {
    position: absolute; left: 0; top: 192px; width: 292px; height: 54px;
    background: var(--slate); color: var(--on-dark);
    padding: 6px 0 0 32px;
  }
  .person-name { font-weight: 700; font-size: 15px; letter-spacing: .5px; }
  .person-role { font-weight: 700; font-size: 11px; margin-top: 1px; }

  .address {
    position: absolute; left: 32px; top: 266px;
    font-size: 12.5px; color: var(--ink);
  }
</style>
</head>
<body>
<main class="stage">
  <section class="card card--front" aria-label="Business card front">
    <div class="brand-name">pexla</div>
    <div class="contact-band"></div>
    <div class="icon-strip"></div>
    <ul class="icon-list" aria-hidden="true">
      <li>
        <svg viewBox="0 0 16 16"><path fill="#fff" d="M3.2 1h2.6l1.3 3.4-1.7 1.2c.8 1.9 2.2 3.3 4.1 4.1l1.2-1.7L14 9.3v2.6c0 1.2-.9 2.1-2.1 2.1C6.4 14 2 9.6 2 4.1 2 2 2.2 1 3.2 1z"/></svg>
      </li>
      <li>
        <svg viewBox="0 0 16 16"><rect x="1.5" y="3.5" width="13" height="9" fill="none" stroke="#fff" stroke-width="1.4"/><path d="M1.5 3.5L8 9l6.5-5.5" fill="none" stroke="#fff" stroke-width="1.4"/></svg>
      </li>
      <li>
        <svg viewBox="0 0 16 16"><g fill="none" stroke="#fff" stroke-width="1.2"><circle cx="8" cy="8" r="6.3"/><ellipse cx="8" cy="8" rx="2.8" ry="6.3"/><path d="M1.7 8h12.6M2.8 4.8h10.4M2.8 11.2h10.4"/></g></svg>
      </li>
    </ul>
    <ul class="contact-list">
      <li>012-345-6789</li>
      <li>info@pexla.com</li>
      <li>www.pexla.com</li>
    </ul>
    <div class="name-band">
      <p class="person-name">JOHN SMITH</p>
      <p class="person-role">Position</p>
    </div>
    <p class="address">Street Name, City Name, Zipcode:012345</p>
  </section>

  <section class="card card--back" aria-label="Business card back">
    <div class="brand-name">pexla</div>
  </section>
</main>
</body>
</html>
```